Business Card for a New Zealand IT Startup

I need a business card for VELTA Holdings. We are a young startup based in New Zealand working in internet marketing and web development. The design should have some element connected to New Zealand, such as wave, koru or silver fern, just don't use a kiwi bird.

```html
<!DOCTYPE html>
<html lang="en">
<head>
<meta charset="utf-8">
<title>VELTA Holdings – Business Card</title>
<link rel="stylesheet" href="https://fonts.googleapis.com/css2?family=Open+Sans:wght@400;600;700&display=swap">
<style>
  :root {
    --backdrop: #3a3b3d;
    --brand-blue: #0a6fc0;
    --brand-blue-deep: #075a9e;
    --accent-orange: #f26522;
    --card-white: #ffffff;
    --ink: #3b3b3b;
    --shadow: rgba(0, 0, 0, 0.45);
  }
  * { box-sizing: border-box; margin: 0; padding: 0; }
  html, body {
    width: 1200px;
    height: 1000px;
    overflow: hidden;
    background: var(--backdrop);
    font-family: "Open Sans", Arial, sans-serif;
  }
  .sheet {
    position: relative;
    width: 1200px;
    height: 1000px;
  }
  .card {
    position: absolute;
    left: 250px;
    width: 700px;
    height: 400px;
    box-shadow: 0 14px 34px var(--shadow);
    overflow: hidden;
  }
  /* Reverse side */
  .card--back {
    top: 60px;
    background: linear-gradient(160deg, var(--brand-blue) 0%, var(--brand-blue-deep) 100%);
    display: flex;
    align-items: center;
    justify-content: center;
    gap: 22px;
  }
  .back-mark {
    width: 120px;
    height: 120px;
    border-radius: 50%;
    background: var(--card-white);
  }
  .back-name {
    color: var(--card-white);
    font-weight: 700;
    font-size: 40px;
    letter-spacing: 1px;
  }
  /* Front side */
  .card--front {
    top: 540px;
    background: var(--card-white);
  }
  .brand {
    position: absolute;
    left: 44px;
    top: 40px;
    color: var(--brand-blue);
    font-weight: 700;
    font-size: 44px;
    line-height: 1;
    letter-spacing: 0.5px;
  }
  .contact {
    position: absolute;
    left: 44px;
    top: 130px;
    color: var(--ink);
    font-size: 17px;
    line-height: 1.3;
    list-style: none;
  }
  .contact li {
    display: flex;
    align-items: center;
    gap: 8px;
  }
  .contact .address { padding-left: 0; }
  .contact svg {
    width: 16px;
    height: 16px;
    flex: none;
    fill: var(--brand-blue);
  }
  .address-block { margin-bottom: 4px; }
  .title-band {
    position: absolute;
    right: 0;
    bottom: 70px;
    width: 300px;
    height: 76px;
    background: var(--brand-blue);
    display: flex;
    flex-direction: column;
    justify-content: center;
    padding-left: 100px;
  }
  .title-badge {
    position: absolute;
    right: 232px;
    bottom: 58px;
    width: 100px;
    height: 100px;
    border-radius: 50%;
    background: var(--brand-blue);
    border: 6px solid var(--card-white);
  }
  .person-name {
    color: var(--card-white);
    font-weight: 700;
    font-size: 24px;
    line-height: 1.1;
  }
  .person-role {
    color: var(--card-white);
    font-size: 19px;
    line-height: 1.15;
    letter-spacing: 0.5px;
  }
</style>
</head>
<body>
<main class="sheet">
  <section class="card card--back" aria-label="Card reverse">
    <span class="back-mark" aria-hidden="true"></span>
    <span class="back-name">VELTA Holdings</span>
  </section>

  <section class="card card--front" aria-label="Card front">
    <div class="brand">VELTA Holdings</div>

    <ul class="contact">
      <li class="address-block">27 Harbour View Road<br>Wellington 6011, NZ</li>
      <li>
        <svg viewBox="0 0 16 16" aria-hidden="true"><path d="M3 1h3l1 4-2 1.5a9 9 0 0 0 4.5 4.5L11 9l4 1v3a2 2 0 0 1-2 2C6.4 15 1 9.6 1 3a2 2 0 0 1 2-2z"/></svg>
        021 482 7716
      </li>
      <li>
        <svg viewBox="0 0 16 16" aria-hidden="true"><path d="M4 0h8a1 1 0 0 1 1 1v14a1 1 0 0 1-1 1H4a1 1 0 0 1-1-1V1a1 1 0 0 1 1-1zm1 2v10h6V2zm3 11a1 1 0 1 0 0 2 1 1 0 0 0 0-2z"/></svg>
        022 591 3048
      </li>
      <li>
        <svg viewBox="0 0 16 16" aria-hidden="true"><path d="M4 0h8v5H4zM1 6h14v7h-3v3H4v-3H1zm5 6v2h4v-2z"/></svg>
        04 386 2295
      </li>
      <li>
        <svg viewBox="0 0 16 16" aria-hidden="true"><path d="M0 3h16v10H0zm1.5 1.2L8 9l6.5-4.8V4h-13z"/></svg>
        mara@veltaholdings.com
      </li>
      <li>
        <svg viewBox="0 0 16 16" aria-hidden="true"><path d="M8 0a8 8 0 1 0 0 16A8 8 0 0 0 8 0zm0 1.5c.8 0 1.8 1.9 2 5H6c.2-3.1 1.2-5 2-5zM6 8h4c-.2 3.6-1.2 6.5-2 6.5S6.2 11.6 6 8zM2 8h2.5c.1 2 .5 3.8 1 5A6.5 6.5 0 0 1 2 8zm9.5 0H14a6.5 6.5 0 0 1-3.5 5c.5-1.2.9-3 1-5zM2 6.5A6.5 6.5 0 0 1 5.5 2c-.5 1.2-.9 2.8-1 4.5zm9.5 0c-.1-1.7-.5-3.3-1-4.5A6.5 6.5 0 0 1 14 6.5z"/></svg>
        www.veltaholdings.com
      </li>
    </ul>

    <div class="title-band">
      <span class="person-name">MARA TANE</span>
      <span class="person-role">PRESIDENT</span>
    </div>
    <span class="title-badge" aria-hidden="true"></span>
  </section>
</main>
</body>
</html>
```